Vensol Holdings Web Design

Vensol Holdings Limited Shenzhen

This project is a 10 page launch website.
Our client is seeking a contemporary homepage design for a Holdings company. Once we are happy with the homepage design and select designer we will request a secondary page design.

Please see attached company LOGO for an idea of style, it incorporates the traditional Chinese furniture lattice work. The Corvel crest website is one of our clients favorite so we would like to see a similar homepage design to this website.

Use the websites below for reference purpose. The first two are Chinese and the second two are international. We would like to see elements of both but more focus on international design.

http://www.evergrande.com/http://www.taurenfield.com/pub/default.aspx http://www.corvelcrest.com/zh/maldives_lorinhaven/
http://www.quelba-studio.com
http://media-cache-ex0.snapvalu.com/originals/71/a3/19/71a319c5b2d04e8f6a17c3b9e5d0f4a1.jpg

Company Background
VENSOL HOLDINGS, located in Qianhai, China, is a new real-estate project operator, structuring urban-rural real-estate investment and development, and industrial fund investment. The company also invests in supply chain management and supporting infrastructures. To create new spaces and livable cities Vensol Holdings develop win-win strategic partnerships with a number of institutions. Currently cooperating with Tianjing North Lumore, China urban and rural integrated demonstration.

Target Market(s)

B2B property investment. Target market customers are senior level management/decision makers of large corporations. Focusing geographically on the domestic market first and expanding internationally in 2nd and 3rd years.

Industry/Entity Type

Investment

Requirements
Must have
• Since this is a new company, we would like to the website representing growth and power, E.g. like a growing tree.
Should not have
• Low-level vectors such as curency symbols, American dollar.

```html
<!DOCTYPE html>
<html lang="en">
<head>
<meta charset="utf-8">
<title>Vensol Holdings</title>
<link href="https://fonts.googleapis.com/css2?family=Open+Sans:wght@400;600;700&family=Questrial&display=swap" rel="stylesheet">
<style>
:root{
  --sky:#00aeef;
  --navy:#334075;
  --gold:#c9a24e;
  --gold-light:#e9c84a;
  --gold-dark:#c99f1c;
  --cream:#f3ecd9;
  --white:#ffffff;
  --hero-sky:#a9cdea;
  --hero-cloud:#e4edf4;
  --hero-tree:#5e8a36;
  --hero-leaf:#8cb64a;
  --hero-water:#3f5a3a;
  --city-deep:#0b35b0;
  --city-sky:#4f86c9;
  --city-haze:#8fb2d6;
  --city-night:#23304f;
  --city-glow:#b9784a;
}
*{box-sizing:border-box;margin:0;padding:0}
html,body{width:1046px;height:1200px;overflow:hidden;background:var(--white)}
.canvas{position:relative;width:1046px;height:1200px;overflow:hidden;font-family:"Questrial",sans-serif;color:var(--white)}
.top-band{position:absolute;left:0;top:0;width:1046px;height:79px;background:var(--sky);border-bottom:1px solid #a89a6a}
.site-header{position:absolute;left:0;top:79px;width:1046px;height:157px;background:var(--navy)}
.brand{position:absolute;left:58px;top:23px;width:130px;text-align:center;font-family:"Open Sans",sans-serif;font-weight:400;color:var(--gold);font-size:14px;letter-spacing:.3px}
.brand-circle{display:block;width:74px;height:74px;margin:0 auto 8px;border:2px solid var(--gold);border-radius:50%}
.search{position:absolute;left:663px;top:118px;display:flex;gap:6px}
.search-field{width:215px;height:27px;background:var(--cream);border:2px solid #d8c48c;border-radius:3px}
.search-button{width:107px;height:27px;border-radius:3px;background:linear-gradient(#dcc078,#b9923c);display:flex;align-items:center;justify-content:center;gap:5px;font-family:"Open Sans",sans-serif;font-size:12px;font-weight:600;color:var(--white)}
.main-nav{position:absolute;right:56px;top:204px;display:flex;gap:11px;font-family:"Open Sans",sans-serif;font-size:12.4px;color:var(--white);white-space:nowrap}
.hero{position:absolute;left:0;top:236px;width:1046px;height:378px;
  background:
    radial-gradient(ellipse 260px 90px at 840px 150px,rgba(140,182,74,.75),transparent 70%),
    radial-gradient(ellipse 220px 90px at 230px 150px,rgba(140,182,74,.7),transparent 70%),
    radial-gradient(ellipse 120px 60px at 420px 220px,rgba(214,222,226,.85),transparent 70%),
    linear-gradient(180deg,var(--hero-sky) 0%,var(--hero-cloud) 22%,#c7dbe9 30%,var(--hero-leaf) 38%,var(--hero-tree) 55%,#6f8f6a 72%,var(--hero-water) 100%)}
.hero-title{position:absolute;left:57px;top:278px;font-family:"Open Sans",sans-serif;font-weight:400;font-size:21px;color:var(--gold)}
.hero-sub{position:absolute;left:57px;top:311px;font-family:"Open Sans",sans-serif;font-size:12px;color:var(--gold)}
.city{position:absolute;left:0;top:614px;width:1046px;height:548px;
  background:
    radial-gradient(ellipse 420px 120px at 500px 440px,rgba(185,120,74,.55),transparent 70%),
    radial-gradient(ellipse 300px 90px at 160px 430px,rgba(185,120,74,.45),transparent 70%),
    linear-gradient(180deg,transparent 0%,transparent 52%,rgba(35,48,79,.55) 70%,var(--city-night) 100%),
    linear-gradient(110deg,var(--city-deep) 0%,var(--city-sky) 38%,var(--city-haze) 70%,var(--sky) 100%)}
.about{position:absolute;left:55px;top:640px;width:580px;font-size:12.3px;line-height:19.5px}
.about p+p{margin-top:19px}
.about strong{font-family:"Open Sans",sans-serif;font-weight:700}
.divider-v{position:absolute;left:678px;top:645px;width:1px;height:310px;background:rgba(255,255,255,.7)}
.aside{position:absolute;left:700px;width:300px}
.contact{top:642px;font-size:12px;line-height:15px}
.contact h2,.links h2{font-family:"Questrial",sans-serif;font-weight:400;font-size:22px;line-height:26px}
.contact p+p{margin-top:14px}
.divider-h{position:absolute;left:700px;top:786px;width:290px;height:1px;background:rgba(255,255,255,.7)}
.links{top:800px;font-size:12px;line-height:15px}
.links ul{list-style:none;margin-top:14px}
.actions{position:absolute;left:56px;top:834px;display:flex;gap:11px}
.action{width:180px;height:86px;border:2px solid #d8b85a;border-radius:4px;background:linear-gradient(180deg,#f0dc8a 0%,#e5c94c 42%,var(--gold-dark) 43%,var(--gold-light) 100%);font-family:"Open Sans",sans-serif;font-size:17px;line-height:24px;text-align:center;padding-top:18px;color:var(--white)}
.site-footer{position:absolute;left:0;top:1162px;width:1046px;height:38px;background:linear-gradient(90deg,var(--sky),#2f4f9a 50%,var(--sky));display:flex;justify-content:center;align-items:center;gap:8px}
.social{width:23px;height:23px;border:2px solid var(--white);border-radius:50%}
</style>
</head>
<body>
<div class="canvas">
  <div class="top-band"></div>
  <header class="site-header">
    <div class="brand"><span class="brand-circle"></span>Vensol Holdings</div>
  </header>
  <form class="search" role="search">
    <div class="search-field"></div>
    <div class="search-button">
      <svg width="16" height="16" viewBox="0 0 16 16" aria-hidden="true"><circle cx="8" cy="8" r="7" fill="none" stroke="#fff" stroke-width="1.3"/><circle cx="7.3" cy="7.3" r="2.8" fill="none" stroke="#fff" stroke-width="1.3"/><line x1="9.3" y1="9.3" x2="11.5" y2="11.5" stroke="#fff" stroke-width="1.5"/></svg>
      SEARCH
    </div>
  </form>
  <nav class="main-nav">
    <span>HOME</span><span>ABOUT VENSOL HOLDINGS</span><span>NEWS CENTER</span><span>OUR PROJECTS</span><span>GROUP BUSINESS</span><span>CORPORATE CULTURE</span><span>CONTACT US</span>
  </nav>

  <div class="hero" role="img" aria-label="Photo of a Chinese garden with a red-roofed pavilion, rocks, willow trees and a calm lake under a blue sky"></div>
  <h1 class="hero-title">Vensol Holdings</h1>
  <p class="hero-sub">Lorem ipsum dolor sit amet, consectetur adipiscing elit</p>

  <div class="city" role="img" aria-label="Photo of a city skyline at dusk with a stadium and lit streets"></div>
  <section class="about">
    <p><strong>VENSOL HOLDINGS</strong> located in Qianhai, China, is a new real-estate project operator, structuring urban-rural real-estate investment and development, and industrial fund investment.</p>
    <p>The company also invests in supply chain management and supporting infrastructures.<br>To create new spaces and livable cities Vensol Holdings develop win-win strategic partnerships with a number of institutions. Currently cooperating with Tianjing North Lumore, China urban and rural integrated demonstration.</p>
  </section>
  <div class="divider-v"></div>
  <section class="aside contact">
    <h2>Contact Information</h2>
    <p>Suite 208, Harbourline Boulevard<br>Qianhai, China</p>
    <p>Tel +0755 480 2913<br>Fax +0755 480 2914<br>E-mail info@vensolholdings.com</p>
  </section>
  <div class="divider-h"></div>
  <section class="aside links">
    <h2>Lorem ipsum dolor sit amet,</h2>
    <p>consectetur adipiscing elit.<br>Nam non malesuada enim. Suspendisse potenti.</p>
    <ul>
      <li>About Vensol Holdings</li>
      <li>Architecture</li>
      <li>Corporate Social Responsibility</li>
      <li>Meet the General Manager</li>
    </ul>
  </section>
  <div class="actions">
    <div class="action">LOREM IPSUM<br>DOLOR</div>
    <div class="action">LOREM IPSUM<br>DOLOR</div>
    <div class="action">LOREM IPSUM<br>DOLOR</div>
  </div>

  <footer class="site-footer" aria-label="Social links">
    <span class="social"></span><span class="social"></span><span class="social"></span><span class="social"></span>
  </footer>
</div>
</body>
</html>
```